Landing Page / Waitlist

I would like a landing page for people to sign up for a waiting list. The text on the page should include (but is not limited to):
1) Main point: The accounting system you'll love
2) Secondary points:
a. Ruthlessly efficient
b. Quietly intelligent
c. Driven by AI
I've attached a file of our logo

The design should be simple, clean, and innovative - this is an ai company

```html
<!DOCTYPE html>
<html lang="en">
<head>
<meta charset="utf-8">
<title>LedgerGlow — Join the Waitlist</title>
<link rel="stylesheet" href="https://fonts.googleapis.com/css2?family=Kumbh+Sans:wght@300;400;500;600;700&display=swap">
<style>
  :root {
    --sky: #6dd3fb;
    --blue-mid: #3d86ef;
    --blue-deep: #2f6deb;
    --white: #ffffff;
    --card: #cbdff7;
    --ink: #111827;
    --icon-soft: #a9cdf6;
    --icon-strong: #5aa6ef;
    --button: #3a77dc;
  }
  * { box-sizing: border-box; margin: 0; padding: 0; }
  html, body { width: 950px; height: 1200px; overflow: hidden; }
  body {
    font-family: "Kumbh Sans", sans-serif;
    color: var(--white);
  }
  .page {
    position: relative;
    width: 950px;
    height: 1200px;
    background:
      radial-gradient(circle at 0% 0%, var(--sky) 0%, rgba(109,211,251,0) 45%),
      linear-gradient(160deg, var(--blue-mid) 0%, var(--blue-deep) 70%);
    overflow: hidden;
  }
  .brand {
    position: absolute;
    top: 270px;
    left: 0;
    width: 100%;
    text-align: center;
    font-size: 96px;
    font-weight: 600;
    letter-spacing: -1px;
    line-height: 1;
    color: var(--white);
  }
  .headline {
    position: absolute;
    top: 412px;
    left: 0;
    width: 100%;
    text-align: center;
    font-size: 70px;
    line-height: 97px;
    color: var(--white);
  }
  .headline .strong { font-weight: 600; }
  .headline .light { font-weight: 300; }
  .features {
    position: absolute;
    top: 677px;
    left: 64px;
    display: flex;
    gap: 24px;
  }
  .feature-card {
    width: 258px;
    height: 263px;
    background: var(--card);
    border-radius: 20px;
    text-align: center;
    color: var(--ink);
  }
  .feature-icon {
    display: block;
    width: 66px;
    height: 66px;
    margin: 42px auto 0;
    border-radius: 50%;
    background: radial-gradient(circle at 35% 70%, var(--icon-soft) 0%, var(--icon-strong) 100%);
    opacity: 0.8;
  }
  .feature-label {
    margin-top: 40px;
    font-size: 21px;
    font-weight: 500;
    line-height: 43px;
    letter-spacing: 0.3px;
  }
  .signup {
    position: absolute;
    top: 1033px;
    left: 45px;
    width: 861px;
    height: 70px;
    background: var(--white);
    border-radius: 10px;
    display: flex;
    align-items: center;
    padding: 5px;
  }
  .signup-input {
    flex: 1;
    padding-left: 24px;
    font-size: 20px;
    font-weight: 500;
    color: var(--ink);
    letter-spacing: 0.3px;
  }
  .signup-button {
    width: 298px;
    height: 60px;
    border-radius: 8px;
    background: var(--button);
    color: var(--white);
    display: flex;
    align-items: center;
    justify-content: center;
    font-size: 21px;
    font-weight: 500;
    letter-spacing: 0.4px;
  }
</style>
</head>
<body>
  <main class="page">
    <div class="brand">LedgerGlow</div>

    <h1 class="headline">
      <span class="strong">The Accounting</span><br>
      <span class="strong">System</span> <span class="light">You'll Love</span>
    </h1>

    <section class="features">
      <div class="feature-card">
        <span class="feature-icon" role="img" aria-label="Clock with gear icon for efficiency"></span>
        <p class="feature-label">RUTHLESSLY<br>EFFICIENT</p>
      </div>
      <div class="feature-card">
        <span class="feature-icon" role="img" aria-label="Head with circuit lines icon for intelligence"></span>
        <p class="feature-label">QUIETLY<br>INTELLIGENT</p>
      </div>
      <div class="feature-card">
        <span class="feature-icon" role="img" aria-label="AI chip icon"></span>
        <p class="feature-label">DRIVEN BY<br>AI</p>
      </div>
    </section>

    <form class="signup">
      <span class="signup-input">ENTER EMAIL ADDRESS</span>
      <span class="signup-button">JOIN THE WAITLIST</span>
    </form>
  </main>
</body>
</html>
```